Website Home Page for Women's Health Medical Office

Redesign existing homepage for website using existing logo. Current website location is www.meadowcrestwomens.com. Please give it a modern, streamlined, playful feel.

Please give it a feminine feel and make it bright and cheerful using logo colors.

Target Market(s)

Women between the ages of 25-45

Industry/Entity Type

Medical Office

Coding

Coded - Design and coding required

Number of Pages Required

1 page

Font styles to use
Sans Serif
Other font styles liked:
• SEGOI UI script for text and GIL SANS for bold (or their equivilent)

Colors
E54698
E96AAD
F1A4CE
F9D9EA
FCEFF6

Requirements
Must have
• Existing logo. Logo Colors. Feminine, cheerful, simple design. all relevant contact information
Nice to have
• clean lines and streamlined look
Should not have
• Cluttered

```html
<!DOCTYPE html>
<html lang="en">
<head>
<meta charset="utf-8">
<title>Meadowcrest OB/GYN – Women's Health</title>
<link href="https://fonts.googleapis.com/css2?family=Montserrat:wght@500;600;700;800&family=Roboto:ital,wght@0,400;0,500;0,700;1,500;1,700&display=swap" rel="stylesheet">
<style>
:root{
  --rose:#e54698;
  --rose-mid:#e96aad;
  --rose-soft:#f1a4ce;
  --blush:#f9d9ea;
  --mist:#fcf0f6;
  --berry:#b3035c;
  --ink:#1a1a1a;
  --text:#5a5a5a;
  --white:#ffffff;
}
*{box-sizing:border-box;margin:0;padding:0}
html,body{width:1200px;height:3731px;overflow:hidden}
body{position:relative;background:var(--white);font-family:'Roboto',sans-serif;color:var(--text)}
.abs{position:absolute}
a{color:inherit;text-decoration:none}

.topbar{left:0;top:0;width:1200px;height:43px;background:var(--rose);color:var(--white);font-size:12px;font-weight:500}
.topbar .item{position:absolute;top:14px;display:flex;align-items:center;gap:10px}
.topbar svg{width:12px;height:12px;fill:var(--white)}

.nav{left:0;top:43px;width:1200px;height:80px;background:var(--white)}
.nav .link{position:absolute;top:34px;font-size:14px;font-weight:500;color:var(--ink);display:flex;align-items:center;gap:8px}
.nav .link.active{color:var(--rose)}
.nav .caret{width:0;height:0;border-left:4px solid transparent;border-right:4px solid transparent;border-top:5px solid var(--ink)}
.search{left:1048px;top:70px;width:30px;height:30px;border-radius:50%;background:var(--rose);display:flex;align-items:center;justify-content:center}
.brand{left:110px;top:43px;width:158px;height:125px;background:var(--white);box-shadow:0 2px 8px rgba(229,70,152,.12);display:flex;flex-direction:column;align-items:center;justify-content:center;gap:6px;z-index:3}
.brand .dot{width:40px;height:40px;border-radius:50%;background:var(--blush)}
.brand .name{font-family:'Montserrat',sans-serif;font-weight:700;font-size:14px;color:var(--rose);text-align:center;line-height:1.2}

.hero{left:0;top:123px;width:1200px;height:760px;background:linear-gradient(90deg,#f5c6de 0%,#f7d0e4 45%,#f3bcd8 100%);overflow:hidden}
.hero-photo{position:absolute;left:610px;top:0;width:590px;height:700px;background:radial-gradient(ellipse at 55% 40%,#e8a9a8 0%,#f0b9cc 45%,rgba(245,198,222,0) 75%)}
.eyebrow{left:114px;top:252px;font-family:'Montserrat',sans-serif;font-weight:700;font-size:26px;color:var(--rose)}
.hero-title{left:110px;top:300px;font-family:'Montserrat',sans-serif;font-weight:700;font-size:50px;line-height:60px;color:var(--ink)}
.hero-text{left:114px;top:448px;width:520px;font-size:18px;line-height:28px;font-weight:500;color:#555}
.btn{display:flex;align-items:center;justify-content:center;gap:10px;background:var(--rose);color:var(--white);border-radius:30px;font-size:13px;font-weight:700;letter-spacing:.2px;box-shadow:0 4px 10px rgba(229,70,152,.25)}
.btn svg{width:13px;height:13px}

.outline-head{font-family:'Montserrat',sans-serif;font-weight:800;font-size:29px;color:#f9cce3;-webkit-text-stroke:1.2px var(--rose-mid);letter-spacing:.2px;line-height:38px}
.rule{width:44px;height:3px;background:var(--rose);border-radius:2px}

.about-art{left:58px;top:960px;width:514px;height:330px;background:radial-gradient(ellipse at 50% 50%,#fde6f1 0%,rgba(255,255,255,0) 70%)}
.about-bg{left:560px;top:840px;width:640px;height:520px;background:radial-gradient(ellipse at 60% 60%,#fbe3ef 0%,rgba(255,255,255,0) 70%)}
.about-copy{left:609px;top:1010px;width:490px;font-size:13.5px;line-height:22.2px;color:#666;text-align:justify}
.about-copy p+p{margin-top:22px}

.services-bg{left:0;top:1440px;width:1200px;height:940px;background:linear-gradient(180deg,#fbd6e8 0%,#fde4f0 60%,#fdeaf3 100%)}
.card{position:absolute;top:1673px;width:234px;height:486px;background:var(--white);border-radius:117px;box-shadow:0 6px 18px rgba(229,70,152,.12);text-align:center}
.card.lift{box-shadow:0 10px 26px rgba(120,30,80,.22)}
.card .photo{position:absolute;left:16px;top:17px;width:202px;height:202px;border-radius:50%}
.card .badge{position:absolute;left:78px;top:143px;width:78px;height:78px;border-radius:50%;background:var(--rose);display:flex;align-items:center;justify-content:center;border:3px solid var(--white)}
.card .badge svg{width:34px;height:34px;fill:var(--white)}
.card h3{position:absolute;left:0;width:100%;top:252px;font-family:'Montserrat',sans-serif;font-weight:700;font-size:17px;color:var(--ink)}
.card .rule{position:absolute;left:95px;top:290px}
.card p{position:absolute;left:20px;top:310px;width:194px;font-size:13px;line-height:22px;color:#666;text-align:justify;text-align-last:center}
.card .go{position:absolute;left:87px;bottom:0;width:60px;height:30px;border-radius:30px 30px 0 0;background:var(--rose);display:flex;align-items:center;justify-content:center}
.card .go svg{width:14px;height:14px;margin-top:4px}

.spec-copy{left:112px;top:2566px;width:978px;font-size:14px;line-height:23px;color:#666;text-align:justify;text-align-last:center}
.spec-copy .hl{color:var(--rose);font-weight:500}

.cta-bg{left:0;top:2833px;width:1200px;height:420px;background:linear-gradient(180deg,#fde8f2 0%,#fbd9ea 100%)}
.cta-sub{left:0;top:2984px;width:1200px;text-align:center;font-style:italic;font-weight:700;font-size:21px;color:var(--rose)}
.cta-main{left:0;top:3020px;width:1200px;text-align:center;font-style:italic;font-weight:700;font-size:26px;color:var(--ink)}

.footer{left:0;top:3290px;width:1200px;height:400px;background:var(--berry)}
.foot-head{font-family:'Roboto',sans-serif;font-weight:700;font-size:18px;color:var(--white)}
.foot-rule{width:30px;height:3px;background:var(--white)}
.field{position:absolute;height:44px;border:1px solid rgba(255,255,255,.55);border-radius:2px;color:var(--white);font-size:13px;padding:14px 12px}
.submit{left:112px;top:3599px;width:132px;height:42px;background:var(--rose);color:var(--white);font-size:13px;font-weight:700;display:flex;align-items:center;justify-content:center}
.contact-row{position:absolute;left:569px;display:flex;align-items:flex-start;gap:18px;color:var(--white);font-size:13px;line-height:19px}
.contact-row .ic{width:34px;height:34px;border-radius:50%;border:1px solid rgba(255,255,255,.5);display:flex;align-items:center;justify-content:center;flex:none}
.contact-row svg{width:13px;height:13px;fill:var(--white)}
.contact-row span{padding-top:6px}
.quick{position:absolute;left:948px;display:flex;align-items:center;gap:18px;color:var(--white);font-size:14px}
.quick svg{width:10px;height:10px}
.copyright{left:0;top:3690px;width:1200px;height:41px;background:var(--rose);color:var(--white);font-size:13px;text-align:center;line-height:41px}
</style>
</head>
<body>

<div class="abs topbar">
  <div class="item" style="left:112px"><svg viewBox="0 0 24 24"><path d="M12 2a7 7 0 0 0-7 7c0 5 7 13 7 13s7-8 7-13a7 7 0 0 0-7-7zm0 9.5A2.5 2.5 0 1 1 12 6.5a2.5 2.5 0 0 1 0 5z"/></svg>1480 Willow Bend Road, Suite 120, Fairhaven, CA 92400</div>
  <div class="item" style="left:584px"><svg viewBox="0 0 24 24"><path d="M6.6 10.8a15 15 0 0 0 6.6 6.6l2.2-2.2a1 1 0 0 1 1-.25 11.4 11.4 0 0 0 3.6.57 1 1 0 0 1 1 1V20a1 1 0 0 1-1 1A17 17 0 0 1 3 4a1 1 0 0 1 1-1h3.5a1 1 0 0 1 1 1c0 1.25.2 2.45.57 3.6a1 1 0 0 1-.25 1z"/></svg>(555) 214-3380</div>
  <div class="item" style="left:754px"><svg viewBox="0 0 24 24"><path d="M6 3h9l3 3v4H6zM3 11h18v9H3zm4 3v2h4v-2zm7 0v2h3v-2z"/></svg>555-214-3381</div>
  <div class="item" style="left:910px"><svg viewBox="0 0 24 24"><path d="M2 5h20v14H2zm2 2v.5l8 5 8-5V7z"/></svg>admin@meadowcrestwomens.com</div>
</div>

<div class="abs nav">
  <a class="link active" style="left:398px">Home</a>
  <a class="link" style="left:497px">About Us</a>
  <a class="link" style="left:618px">Our Services <i class="caret"></i></a>
  <a class="link" style="left:780px">Resources <i class="caret"></i></a>
  <a class="link" style="left:928px">Contact Us</a>
</div>
<div class="abs search"><svg width="12" height="12" viewBox="0 0 24 24" fill="none" stroke="#fff" stroke-width="3"><circle cx="10" cy="10" r="6"/><path d="M15 15l6 6"/></svg></div>
<div class="abs brand"><span class="dot"></span><span class="name">Meadowcrest<br>OB/GYN</span></div>

<section class="abs hero">
  <div class="hero-photo" role="img" aria-label="Photo of a smiling expectant mother in a soft pink sweater holding her belly"></div>
  <svg class="abs" style="left:0;top:560px" width="1200" height="200" viewBox="0 0 1200 200" preserveAspectRatio="none">
    <path d="M0 200 L0 120 C220 200 420 190 640 130 C850 70 1050 40 1200 140 L1200 200 Z" fill="#f9d2e6"/>
    <path d="M0 200 L0 140 C250 210 450 200 660 140 C860 85 1060 60 1200 160 L1200 200 Z" fill="#e54698"/>
    <path d="M0 200 L0 160 C260 210 470 205 680 155 C880 105 1070 90 1200 190 L1200 200 Z" fill="#f1a4ce"/>
    <path d="M0 200 L0 170 C270 210 490 210 700 170 C900 125 1080 120 1200 200 Z" fill="#ffffff"/>
  </svg>
</section>
<div class="abs eyebrow">Welcome To</div>
<h1 class="abs hero-title">Meadowcrest OB/GYN,<br>Fairhaven, CA</h1>
<p class="abs hero-text">At Meadowcrest OB/GYN in Fairhaven, California, we believe better health starts when the patient is educated</p>
<a class="abs btn" style="left:110px;top:536px;width:162px;height:44px">GET STARTED <svg viewBox="0 0 24 24"><circle cx="12" cy="12" r="11" fill="#fff"/><path d="M10 7l5 5-5 5" stroke="#e54698" stroke-width="3" fill="none"/></svg></a>

<div class="abs about-bg"></div>
<div class="abs about-art" role="img" aria-label="Line illustration of a doctor with a tablet talking with a patient"></div>
<h2 class="abs outline-head" style="left:609px;top:888px;width:480px">SERVING WILLOW BEND<br>MEDICAL CENTER</h2>
<div class="abs rule" style="left:609px;top:984px"></div>
<div class="abs about-copy">
  <p>At Meadowcrest OB/GYN in Fairhaven, California, we believe better health starts when the patient is educated. For this reason, we take time to listen to our patients concerns, explain each option available, and to answer any questions our patients may have so that they can make informed decisions. At Meadowcrest OB/GYN, our providers tailor every procedure performed and treatment option recommended to meet the specific needs of our patients. We remain up-to-date on the latest technology and practice guidelines for women's health.</p>
  <p>Our medical providers will take time to give you the personalized health care you deserve. This includes taking time to listen to you and screening you for problems to help ensure that any health issues</p>
</div>
<a class="abs btn" style="left:609px;top:1304px;width:164px;height:44px">LEARN MORE <svg viewBox="0 0 24 24"><circle cx="12" cy="12" r="11" fill="#fff"/><path d="M10 7l5 5-5 5" stroke="#e54698" stroke-width="3" fill="none"/></svg></a>

<div class="abs services-bg"></div>
<svg class="abs" style="left:0;top:1360px" width="1200" height="190" viewBox="0 0 1200 190">
  <path d="M0 0 L1200 0 L1200 60 C1000 60 800 80 600 130 C400 180 200 190 0 110 Z" fill="#ffffff"/>
  <path d="M0 30 C150 130 350 180 560 140 C780 95 1000 70 1200 60 L1200 80 C1000 90 780 115 560 165 C330 210 130 160 0 90 Z" fill="#f1a4ce"/>
  <path d="M0 60 C150 160 350 200 560 160 C780 115 1000 90 1200 80 L1200 95 C1000 110 790 135 560 185 C330 230 130 190 0 120 Z" fill="#e54698"/>
</svg>
<h2 class="abs outline-head" style="left:0;top:1568px;width:1200px;text-align:center">OUR SERVICES</h2>
<div class="abs rule" style="left:578px;top:1622px"></div>

<div class="card" style="left:101px">
  <div class="photo" role="img" aria-label="Photo of an obstetrician consulting with a pregnant patient" style="background:linear-gradient(135deg,#cfd6dc,#e7d4d6)"></div>
  <div class="badge"><svg viewBox="0 0 24 24"><path d="M12 21s-8-5-8-11a4.5 4.5 0 0 1 8-2.8A4.5 4.5 0 0 1 20 10c0 6-8 11-8 11z"/></svg></div>
  <h3>Pregnancy Care</h3><div class="rule"></div>
  <p>Receiving regular care in pregnancy is important for the health of both you and your baby. Our obstetricians work with you every step</p>
  <div class="go"><svg viewBox="0 0 24 24"><circle cx="12" cy="12" r="11" fill="#fff"/><path d="M10 7l5 5-5 5" stroke="#e54698" stroke-width="3" fill="none"/></svg></div>
</div>
<div class="card lift" style="left:356px">
  <div class="photo" role="img" aria-label="Photo of a young woman reading a leaflet at home" style="background:linear-gradient(135deg,#b59383,#e8cdbf)"></div>
  <div class="badge"><svg viewBox="0 0 24 24"><path d="M4 5h16v15H4zM7 2h2v4H7zm8 0h2v4h-2zM6 10v8h12v-8z"/></svg></div>
  <h3>Birth Control</h3><div class="rule"></div>
  <p>Our gynecologists are knowledgeable on all forms of birth control including the IUD, the arm implant, vaginal ring insertion, birth control pills, and more!</p>
  <div class="go"><svg viewBox="0 0 24 24"><circle cx="12" cy="12" r="11" fill="#fff"/><path d="M10 7l5 5-5 5" stroke="#e54698" stroke-width="3" fill="none"/></svg></div>
</div>
<div class="card" style="left:611px">
  <div class="photo" role="img" aria-label="Photo of a woman relaxing in warm sunlight" style="background:linear-gradient(135deg,#c7d1d6,#e9cdb4)"></div>
  <div class="badge"><svg viewBox="0 0 24 24"><path d="M9.5 16.2l-4-4 1.4-1.4 2.6 2.6 7.6-7.6 1.4 1.4z"/></svg></div>
  <h3>Well Woman Exams</h3><div class="rule"></div>
  <p>Our providers will help you to stay healthy by performing a physical exam on you annually. We will screen you for multiple health</p>
  <div class="go"><svg viewBox="0 0 24 24"><circle cx="12" cy="12" r="11" fill="#fff"/><path d="M10 7l5 5-5 5" stroke="#e54698" stroke-width="3" fill="none"/></svg></div>
</div>
<div class="card" style="left:865px">
  <div class="photo" role="img" aria-label="Photo of a woman meditating in a bright living room" style="background:linear-gradient(135deg,#dfe3e8,#c9b9c6)"></div>
  <div class="badge"><svg viewBox="0 0 24 24"><path d="M12 2l2.9 6.3 6.9.7-5.2 4.6 1.5 6.8L12 17l-6.1 3.4 1.5-6.8L2.2 9l6.9-.7z"/></svg></div>
  <h3>Women's Health</h3><div class="rule"></div>
  <p>Whether you are dealing with painful or irregular periods, fibroids, or other women's health issues, we can help. We offer a variety</p>
  <div class="go"><svg viewBox="0 0 24 24"><circle cx="12" cy="12" r="11" fill="#fff"/><path d="M10 7l5 5-5 5" stroke="#e54698" stroke-width="3" fill="none"/></svg></div>
</div>

<a class="abs btn" style="left:500px;top:2250px;width:198px;height:46px">VIEW ALL SERVICES <svg viewBox="0 0 24 24"><circle cx="12" cy="12" r="11" fill="#fff"/><path d="M10 7l5 5-5 5" stroke="#e54698" stroke-width="3" fill="none"/></svg></a>

<svg class="abs" style="left:0;top:2290px" width="1200" height="190" viewBox="0 0 1200 190">
  <path d="M0 80 C200 150 420 120 640 70 C860 20 1060 20 1200 110 L1200 190 L0 190 Z" fill="#ffffff"/>
  <path d="M0 70 C260 110 430 100 640 45 C860 -5 1060 10 1200 90 L1200 120 C1060 40 860 30 640 80 C430 130 260 140 0 90 Z" fill="#e54698"/>
  <path d="M300 110 C460 100 560 70 700 45 C880 10 1060 30 1200 110 L1200 135 C1060 60 880 40 700 75 C560 100 460 115 300 110 Z" fill="#f1a4ce"/>
</svg>

<h2 class="abs outline-head" style="left:0;top:2488px;width:1200px;text-align:center">YOUR OB/GYN SPECIALISTS</h2>
<div class="abs rule" style="left:578px;top:2542px"></div>
<div class="abs spec-copy">Meadowcrest OB/GYN offers you the best care possible in a personalized setting. We are currently accepting patients. Call our office now to make an appointment. Meadowcrest OB/GYN (located near Willow Bend Hospital in Fairhaven, CA) is a medical office that specializes in Christ-centered healthcare for women of all ages. <span class="hl">Our team of exclusively female providers</span> have years of experience taking care of women with a variety of pregnancy and gynecology concerns.<br>Whether you need a routine examination, help during your pregnancy, have questions on birth control, or another female concern, we offer the best care possible for our patients. That is why better health starts here. Our office provides you with an environment where you can feel comfortable and where you know you will be in good hands. Our providers are leaders women's health. Dr. Harlow is a board certified obstetrician and gynecologist. Dr. Navarro is a board eligible obstetrician and gynecologist.</div>

<div class="abs cta-bg"></div>
<h2 class="abs outline-head" style="left:0;top:2904px;width:1200px;text-align:center">NOW ACCEPTING NEW PATIENTS</h2>
<div class="abs rule" style="left:578px;top:2959px"></div>
<div class="abs cta-sub">Better Health Starts Here!</div>
<div class="abs cta-main">Click Here for an Appointment or Call Us At</div>
<a class="abs btn" style="left:500px;top:3082px;width:201px;height:52px;font-size:17px;font-weight:500">(555) 214-3380 <svg viewBox="0 0 24 24"><rect x="3" y="3" width="18" height="18" rx="3" fill="#fff"/><path d="M9 8l2 2-1 1.5a6 6 0 0 0 2.5 2.5l1.5-1 2 2-1.5 1.5A8 8 0 0 1 7.5 9.5z" fill="#e54698"/></svg></a>

<div class="abs footer"></div>
<svg class="abs" style="left:0;top:3160px" width="1200" height="180" viewBox="0 0 1200 180">
  <path d="M0 0 L1200 0 L1200 30 C1000 110 760 150 520 140 C300 130 130 80 0 40 Z" fill="#fbd9ea"/>
  <path d="M0 40 C130 80 300 130 520 140 C760 150 1000 110 1200 30 L1200 180 L0 180 Z" fill="#e54698"/>
  <path d="M0 75 C150 130 320 165 540 165 C780 160 1000 110 1200 50 L1200 180 L0 180 Z" fill="#e96aad"/>
  <path d="M0 100 C160 150 330 180 560 178 C800 172 1010 125 1200 70 L1200 180 L0 180 Z" fill="#b3035c"/>
</svg>

<div class="abs foot-head" style="left:112px;top:3362px">Get In Touch</div>
<div class="abs foot-rule" style="left:112px;top:3396px"></div>
<div class="field" style="left:112px;top:3421px;width:174px">Name</div>
<div class="field" style="left:297px;top:3421px;width:174px">Company</div>
<div class="field" style="left:112px;top:3478px;width:174px">Email</div>
<div class="field" style="left:297px;top:3478px;width:174px">Zipcode</div>
<div class="field" style="left:112px;top:3536px;width:359px">State</div>
<div class="abs submit">SUBMIT NOW</div>

<div class="abs foot-head" style="left:569px;top:3362px">Contact Us</div>
<div class="abs foot-rule" style="left:569px;top:3396px"></div>
<div class="contact-row" style="top:3418px"><i class="ic"><svg viewBox="0 0 24 24"><path d="M12 2a7 7 0 0 0-7 7c0 5 7 13 7 13s7-8 7-13a7 7 0 0 0-7-7zm0 9.5A2.5 2.5 0 1 1 12 6.5a2.5 2.5 0 0 1 0 5z"/></svg></i><span>1480 Willow Bend Road, Suite 120,<br>Fairhaven, CA 92400</span></div>
<div class="contact-row" style="top:3471px"><i class="ic"><svg viewBox="0 0 24 24"><path d="M6.6 10.8a15 15 0 0 0 6.6 6.6l2.2-2.2a1 1 0 0 1 1-.25 11.4 11.4 0 0 0 3.6.57 1 1 0 0 1 1 1V20a1 1 0 0 1-1 1A17 17 0 0 1 3 4a1 1 0 0 1 1-1h3.5a1 1 0 0 1 1 1c0 1.25.2 2.45.57 3.6a1 1 0 0 1-.25 1z"/></svg></i><span>(555) 214-3380</span></div>
<div class="contact-row" style="top:3523px"><i class="ic"><svg viewBox="0 0 24 24"><path d="M6 3h9l3 3v4H6zM3 11h18v9H3zm4 3v2h4v-2zm7 0v2h3v-2z"/></svg></i><span>555-214-3381</span></div>
<div class="contact-row" style="top:3574px"><i class="ic"><svg viewBox="0 0 24 24"><path d="M2 5h20v14H2zm2 2v.5l8 5 8-5V7z"/></svg></i><span>admin@meadowcrestwomens.com</span></div>

<div class="abs foot-head" style="left:948px;top:3362px">Quick Links</div>
<div class="abs foot-rule" style="left:948px;top:3396px"></div>
<div class="quick" style="top:3418px"><svg viewBox="0 0 10 10" fill="none" stroke="#fff" stroke-width="1.5"><path d="M1 1l4 4-4 4M5 1l4 4-4 4"/></svg>Home</div>
<div class="quick" style="top:3448px"><svg viewBox="0 0 10 10" fill="none" stroke="#fff" stroke-width="1.5"><path d="M1 1l4 4-4 4M5 1l4 4-4 4"/></svg>Services</div>
<div class="quick" style="top:3478px"><svg viewBox="0 0 10 10" fill="none" stroke="#fff" stroke-width="1.5"><path d="M1 1l4 4-4 4M5 1l4 4-4 4"/></svg>Resources</div>
<div class="quick" style="top:3508px"><svg viewBox="0 0 10 10" fill="none" stroke="#fff" stroke-width="1.5"><path d="M1 1l4 4-4 4M5 1l4 4-4 4"/></svg>About Us</div>
<div class="quick" style="top:3538px"><svg viewBox="0 0 10 10" fill="none" stroke="#fff" stroke-width="1.5"><path d="M1 1l4 4-4 4M5 1l4 4-4 4"/></svg>Healthcare</div>
<div class="quick" style="top:3568px"><svg viewBox="0 0 10 10" fill="none" stroke="#fff" stroke-width="1.5"><path d="M1 1l4 4-4 4M5 1l4 4-4 4"/></svg>Contact Us</div>

<div class="abs copyright">© 2022 Meadowcrest OB/GYN. All Rights Reserved</div>

</body>
</html>
```